KBT Business Cards

We require business cards for our business. We would like a matte black back to the card, with our logo centred in the middle. The front side of the card is open to design.

Target Market(s)

Clients looking for legal services (professional)

Industry/Entity Type

Legal

Contact Information for Business Card

Doran Kelbrath
Partner
Mobile: 0461 738 524
Email: doran@kbtlaw.co
Website: www.kbtlaw.co
Level 3, 118 Wendmore Street
Sydney NSW 2000

Font styles to use
Other font styles liked:
• Avenir

Colors
f04a50
ffffff
1b1b1b

Requirements
Must have
• Black back with logo included in the centre of the card.
• Our font is Avenir.

```html
<!DOCTYPE html>
<html lang="en">
<head>
<meta charset="UTF-8">
<title>KBT Legal Business Cards</title>
<link href="https://fonts.googleapis.com/css2?family=Nunito+Sans:wght@400;700;800&display=swap" rel="stylesheet">
<style>
  :root {
    --backdrop: #121212;
    --card: #1b1b1b;
    --accent: #f04a50;
    --white: #ffffff;
    --muted: #d8d8d8;
    --silver: #9a9a9a;
  }
  * { margin: 0; padding: 0; box-sizing: border-box; }
  html, body { width: 1200px; height: 900px; overflow: hidden; }
  body {
    background: var(--backdrop);
    font-family: "Nunito Sans", "Avenir", sans-serif;
    position: relative;
  }
  .card {
    position: absolute;
    left: 320px;
    width: 560px;
    height: 320px;
    background: var(--card);
    border-radius: 4px;
    overflow: hidden;
  }
  .card--back { top: 110px; }
  .card--front { top: 470px; }

  .brand {
    position: absolute;
    display: flex;
    align-items: center;
    gap: 14px;
  }
  .card--back .brand {
    left: 50%; top: 50%;
    transform: translate(-50%, -50%);
  }
  .brand__square {
    width: 26px; height: 26px;
    background: var(--silver);
  }
  .brand__name {
    font-weight: 800;
    font-size: 30px;
    letter-spacing: 2px;
    color: var(--silver);
  }

  .front__info {
    position: absolute;
    left: 48px; top: 38px;
  }
  .front__firm {
    font-weight: 800;
    font-size: 40px;
    line-height: 1;
    letter-spacing: 1px;
    color: var(--white);
  }
  .person__name {
    margin-top: 28px;
    font-weight: 700;
    font-size: 22px;
    letter-spacing: 0.5px;
    color: var(--accent);
  }
  .person__role {
    font-size: 15px;
    color: var(--muted);
    margin-top: 2px;
  }
  .address {
    margin-top: 20px;
    font-size: 15px;
    line-height: 1.45;
    color: var(--muted);
    font-style: normal;
  }
  .contact {
    list-style: none;
    margin-top: 16px;
    font-size: 15px;
    line-height: 1.5;
    color: var(--muted);
  }
  .contact li { display: flex; align-items: center; gap: 10px; }
  .contact svg { width: 12px; height: 12px; flex: none; }

  .front__mark {
    position: absolute;
    right: 60px; top: 80px;
    width: 170px; height: 170px;
    background: linear-gradient(135deg, #2a2a2a 0%, #6a6a6a 55%, #cfcfcf 100%);
  }
</style>
</head>
<body>

<section class="card card--back" aria-label="Card back">
  <div class="brand">
    <span class="brand__square"></span>
    <span class="brand__name">KBT LEGAL</span>
  </div>
</section>

<section class="card card--front" aria-label="Card front">
  <div class="front__info">
    <div class="front__firm">KBT LEGAL</div>
    <div class="person__name">DORAN KELBRATH</div>
    <div class="person__role">General Manager</div>
    <address class="address">
      Level 3, 118 Wendmore Street<br>
      Sydney NSW 2000
    </address>
    <ul class="contact">
      <li>
        <svg viewBox="0 0 12 12" aria-hidden="true"><path d="M3 1 L5 3.5 L4 5 Q5 7 7 8 L8.5 7 L11 9 L9.5 11 Q4 10.5 1 2.5 Z" fill="var(--accent)"/></svg>
        0461 738 524
      </li>
      <li>
        <svg viewBox="0 0 12 12" aria-hidden="true"><rect x="1" y="2.5" width="10" height="7" fill="none" stroke="var(--accent)" stroke-width="1.3"/><path d="M1 2.5 L6 6.5 L11 2.5" fill="none" stroke="var(--accent)" stroke-width="1.3"/></svg>
        doran@kbtlaw.co
      </li>
      <li>
        <svg viewBox="0 0 12 12" aria-hidden="true"><circle cx="6" cy="6" r="5" fill="none" stroke="var(--accent)" stroke-width="1.2"/><ellipse cx="6" cy="6" rx="2.2" ry="5" fill="none" stroke="var(--accent)" stroke-width="1"/><line x1="1" y1="6" x2="11" y2="6" stroke="var(--accent)" stroke-width="1"/></svg>
        www.kbtlaw.co
      </li>
    </ul>
  </div>
  <div class="front__mark" role="img" aria-label="Brand mark area"></div>
</section>

</body>
</html>
```